Help our Sugar Loom find our winning design! We're looking for a business card....

We’re a Sugar Loom in NY specializing in custom-made cakes and unique desserts.
Our cakes combine flavor and art, each designed to match customer’s special event and theme.
We’d like a unique business card with a clean design that will combine French chic and artistic look & feel.
We’d like to differentiate ourselves from standard bakeries, please don’t offer cupcake images :-)
Our logo is peach-pink and brown and we’d love to use these colors ( . Another color that can be added is gold - or feel free to suggest!

Target Market(s)

Women, ages 25-55

Industry/Entity Type

Boutique

Contact Information for Business Card

Text on card:
Logo
Sugar Loom by Dana Welch

www.sugarloomsweets.com
hello@sugarloom.com
(516) 555-0147
F – sugarloomnyc
IG - sugarloom_ny

Font styles to use
Sans Serif
Script

Requirements
Must have
• Logo
• Clean look
• French chic and artistic look & feel.
Nice to have
• Damask pattern
Should not have
• Cupcake images

```html
<!DOCTYPE html>
<html lang="en">
<head>
<meta charset="utf-8">
<title>Sugar Loom – Business Card</title>
<link rel="stylesheet" href="https://fonts.googleapis.com/css2?family=Tinos:wght@400;700&display=swap">
<style>
  :root {
    --card-bg: #4a403d;
    --card-bg-deep: #3f3633;
    --plaque: #a5928c;
    --plaque-edge: #8c7872;
    --cocoa: #4b2f27;
    --cream: #f6e39c;
    --peach: #f2a595;
  }
  html, body {
    margin: 0;
    padding: 0;
    overflow: hidden;
    background: var(--card-bg);
  }
  .card {
    position: relative;
    width: 1200px;
    height: 720px;
    overflow: hidden;
    font-family: "Tinos", "Times New Roman", serif;
  }
  .damask-field {
    position: absolute;
    inset: 0;
    background: radial-gradient(ellipse at 50% 45%, var(--card-bg) 0%, var(--card-bg-deep) 100%);
  }
  .plaque {
    position: absolute;
    left: 293px;
    top: 69px;
    width: 608px;
    height: 406px;
    filter: drop-shadow(0 2px 6px rgba(0,0,0,0.35));
  }
  .brand-name {
    position: absolute;
    left: 293px;
    top: 276px;
    width: 608px;
    margin: 0;
    text-align: center;
    font-size: 48px;
    font-weight: 400;
    line-height: 1;
    color: var(--cocoa);
  }
  .details {
    position: absolute;
    left: 0;
    top: 508px;
    width: 1200px;
    margin: 0;
    text-align: center;
    font-size: 31px;
    line-height: 58px;
  }
  .details p { margin: 0; white-space: nowrap; }
  .details .owner { color: var(--cream); }
  .details .social { color: var(--peach); font-weight: 700; }
  .details .contact { color: var(--cream); font-size: 28px; }
  .details .sep { padding: 0 10px; }
</style>
</head>
<body>
  <main class="card">
    <div class="damask-field" role="img" aria-label="Subtle dark brown damask pattern background"></div>

    <svg class="plaque" viewBox="0 0 608 343" preserveAspectRatio="none" aria-hidden="true">
      <path fill="var(--plaque)" stroke="var(--plaque-edge)" stroke-width="2"
        d="M30,70 C55,70 70,55 70,42 L150,42 C170,42 180,2 304,2 C428,2 438,42 458,42 L538,42
           C538,55 553,70 578,70 L578,120 C600,130 606,150 606,171 C606,192 600,212 578,222
           L578,273 C553,273 538,288 538,301 L458,301 C438,301 428,341 304,341
           C180,341 170,301 150,301 L70,301 C70,288 55,273 30,273 L30,222
           C8,212 2,192 2,171 C2,150 8,130 30,120 Z"/>
    </svg>

    <p class="brand-name">Sugar Loom</p>

    <section class="details">
      <p class="owner">Sugar Loom by Dana Welch</p>
      <p class="social">F – sugarloomnyc<span class="sep">·</span>IG – sugarloom_ny</p>
      <p class="contact">www.sugarloomsweets.com<span class="sep">·</span>hello@sugarloom.com<span class="sep">·</span>(516) 555-0147</p>
    </section>
  </main>
</body>
</html>
```